Modern Banner for use on Emails and Electronic letters.

We need a Email banner that we can also uses as a banner on electronic documents . Would be a bonus to be able to use banner on facebook.
The banner should incorporate our logo and company name; The Calvora Group.
We would like an eye catching, modern design.
We are completely open to using colour and/or images along with our logo and company name.
Currently the font for our company name is time new roman but again we are open to suggestions. The company name can be be moved away from the umbrella logo to anywhere in the banner.

Industry/Entity Type

Electronic

Font styles to use
Serif
Sans Serif

Colors

Designer to choose colors to be used in the design.

Requirements
Must have
• Calvora Logo (Umbrella design - Black umbrella on red blocks with a letter on each block spelling VORA.
• Company name: The Calvora Group
• Be Modern and professional.
• Suitable for use as an email banner but can also be used as letterhead on electronic documents.
Nice to have
• Colour and/or images.
• Be able to be used as facebook banner.

```html
<!DOCTYPE html>
<html lang="en">
<head>
<meta charset="utf-8">
<title>The Calvora Group – Letterhead</title>
<link href="https://fonts.googleapis.com/css2?family=Tinos&family=Open+Sans:wght@400;600&display=swap" rel="stylesheet">
<style>
  :root {
    --backdrop: #cfe6b4;
    --paper: #ffffff;
    --brand-red: #e8455f;
    --brand-red-deep: #d8203a;
    --ink: #1b1b1b;
    --ink-soft: #555555;
    --leaf: #8cc63f;
    --leaf-light: #b9dc7c;
    --ghost-grey: #dcdcdc;
    --ghost-red: #f2c4c4;
  }
  html, body {
    margin: 0;
    width: 1200px;
    height: 784px;
    overflow: hidden;
    background: var(--backdrop);
  }
  .canvas {
    position: relative;
    width: 1200px;
    height: 784px;
    display: flex;
    align-items: center;
    justify-content: center;
  }
  .letterhead {
    position: relative;
    width: 524px;
    height: 740px;
    background: var(--paper);
    box-shadow: 0 4px 18px rgba(60, 100, 30, 0.25);
    overflow: hidden;
  }
  .corner {
    position: absolute;
    display: block;
  }
  .corner--top { top: 0; right: 0; width: 200px; height: 150px; }
  .corner--bottom { bottom: 0; left: 0; width: 240px; height: 170px; }

  .brand {
    position: absolute;
    top: 36px;
    right: 34px;
    display: flex;
    align-items: center;
    gap: 8px;
    font-family: "Tinos", "Times New Roman", serif;
    font-size: 22px;
    color: var(--ink);
  }
  .brand__mark {
    width: 12px;
    height: 12px;
    background: var(--brand-red-deep);
  }

  .contact {
    position: absolute;
    top: 300px;
    right: 34px;
    margin: 0;
    padding: 0;
    list-style: none;
    font-family: "Open Sans", Arial, sans-serif;
    font-size: 9.5px;
    line-height: 1.55;
    color: var(--ink-soft);
  }
  .contact__item {
    display: flex;
    align-items: flex-start;
    gap: 6px;
  }
  .contact__icon {
    flex: none;
    width: 8px;
    height: 8px;
    margin-top: 3px;
  }

  .ghost-emblem {
    position: absolute;
    left: 40px;
    top: 250px;
    width: 290px;
    height: 250px;
    border-radius: 48% 52% 40% 40%;
    background: radial-gradient(ellipse at 65% 30%, var(--ghost-grey) 0%, rgba(220,220,220,0.5) 45%, transparent 70%),
                radial-gradient(ellipse at 30% 70%, var(--ghost-red) 0%, rgba(242,196,196,0.4) 35%, transparent 65%);
    opacity: 0.8;
  }

  .partner {
    position: absolute;
    left: 58px;
    bottom: 66px;
    font-family: "Open Sans", Arial, sans-serif;
  }
  .partner__name {
    display: flex;
    align-items: center;
    gap: 7px;
    font-size: 24px;
    font-weight: 600;
    color: var(--leaf);
    margin: 0;
  }
  .partner__mark {
    width: 14px;
    height: 14px;
    border-radius: 50%;
    background: var(--leaf);
  }
  .partner__tagline {
    margin: 2px 0 0 21px;
    font-size: 10.5px;
    color: var(--ink-soft);
  }
</style>
</head>
<body>
<main class="canvas">
  <article class="letterhead">
    <svg class="corner corner--top" viewBox="0 0 200 150" aria-hidden="true">
      <polygon points="110,0 200,0 200,150 186,150 196,26 118,6" fill="var(--brand-red)"/>
    </svg>

    <header class="brand">
      <span class="brand__mark" aria-hidden="true"></span>
      <span class="brand__name">The Calvora Group</span>
    </header>

    <ul class="contact">
      <li class="contact__item">
        <svg class="contact__icon" viewBox="0 0 8 8" aria-hidden="true"><circle cx="4" cy="4" r="4" fill="var(--brand-red)"/></svg>
        <span>Example Avenue, Suite 1000,<br>Marlow, TX 70000</span>
      </li>
      <li class="contact__item">
        <svg class="contact__icon" viewBox="0 0 8 8" aria-hidden="true"><circle cx="4" cy="4" r="4" fill="var(--brand-red)"/></svg>
        <span>(000) 000-4150</span>
      </li>
      <li class="contact__item">
        <svg class="contact__icon" viewBox="0 0 8 8" aria-hidden="true"><circle cx="4" cy="4" r="4" fill="var(--brand-red)"/></svg>
        <span>(000) 000-4151</span>
      </li>
      <li class="contact__item">
        <svg class="contact__icon" viewBox="0 0 8 8" aria-hidden="true"><circle cx="4" cy="4" r="4" fill="var(--brand-red)"/></svg>
        <span>info@calvora.com</span>
      </li>
      <li class="contact__item">
        <svg class="contact__icon" viewBox="0 0 8 8" aria-hidden="true"><circle cx="4" cy="4" r="4" fill="var(--brand-red)"/></svg>
        <span>www.calvora.com</span>
      </li>
    </ul>

    <div class="ghost-emblem" role="img" aria-label="Faint background image of an umbrella above stacked red letter blocks"></div>

    <svg class="corner corner--bottom" viewBox="0 0 240 170" aria-hidden="true">
      <defs>
        <linearGradient id="leaf-band" x1="0" y1="0" x2="1" y2="1">
          <stop offset="0" stop-color="var(--leaf-light)"/>
          <stop offset="1" stop-color="var(--leaf)"/>
        </linearGradient>
      </defs>
      <polygon points="0,0 14,150 240,160 240,170 0,170" fill="url(#leaf-band)"/>
    </svg>

    <footer class="partner">
      <p class="partner__name"><span class="partner__mark" aria-hidden="true"></span>leafline</p>
      <p class="partner__tagline">native woodland care partner</p>
    </footer>
  </article>
</main>
</body>
</html>
```